Creative UI design for web application

I need a new UI design for my web application. It will be used by small and micro business owners to plan & implement growth tactics.

I've attached the current design (which I'm open to be changed) - but in particular I need to design the centre of the screen, where the work actually happens.

There needs to be place for a title (YOUR BUSINESS) and description (say 1-2 paragraphs of text) - and am happy to include icons or imagery where makes sense. It may make sense for the user to be able to upload their business logo and name, for example.

This screen will be used by the business owner to understand the real value they offer potential customers and their point of difference - why they exist and why potential customers should care.

They'll use the information they put into this screen to plan things like their messaging.

Following that, there needs to be 2 sections in the dashboard.

The first section is titled "WHO YOU ARE"

The first section will include a number of boxes that the user can input information into, as follows:

- Logo
- Business name
- Business tag line
- Business vision
- Business bio
- Brand colours (these should end up as swatches based on the colour code they enter) - the colour code for each colour swatch should also be visible.
- Key competitors
- SWOT analysis (boxes to enter their strengths, weaknesses, opportunities and threats).

The second section is titled "WHY YOU EXIST"

The second section will include a number of boxes that the user can input information (text) into, as follows:

- Who are your ideal customers?
- What problem are you trying to solve for them?
- What pain points will this remove for them?
- How do you solve it?
- How else could this problem be solved?
- Who offers these other solutions?
- Why is your solution better?
- How much does your solution cost?
- What value are you providing to justify this cost?
- How will this make their life/job easier/better?

They should be able to write a decent amount of information in the boxes.

There should ideally be a place for a description for each of these text fields (for both section 1 & 2) as well so I can give them a little bit more direction around what to put in the box. Alternatively there could be a little icon (say a question mark or "i") that they could click on to view instructions. The instructions will be around 2-4 sentences long for each text field.

You have 2 options:

a) This all needs to appear on the one screen, and the navigation needs to be visible (as per the example attached but feel free to recreate this navigation)

Note: the page can scroll below the fold - but please provide the design for the full length of the page.

b) Potentially the 2 sections could actually be in 2 different items in the menu - YOUR BUSINESS and YOUR VALUE (which would sit next to YOUR BUSINESS and before YOUR CUSTOMER in the screenshot provided). feel free to design them as 2 separate screens if you prefer.

I have attached a screenshot of the app as it stands today (screen shot 2017) which would still exist in the new design but under a different section (the learn section from the plan2 mockup attached)

I have mocked up how this new screen could look if broken into 2 and that's also attached. If you can make this come to life - and look more engaging that would be helpful! :)

Target Market(s)

Small and micro business owners

Industry/Entity Type

Marketing

Number of Pages Required

1 page

Font styles to use
Sans Serif
Other font styles liked:
• Montserrat

Colors
87cfc6
d2a4cc
ffffff
85cae6
e8e8e8
5c5c5c

Requirements
Must have
• Use of my brand colours: #cc8eb2, #76d6c8, #68c7ff as well as white and #595959. Must be visually pleasing / engaging, designed for desktop (as it's a desktop application), really easy to use / navigate.
• Use font Montserrat light & Montserrat Regular or Bold. Mostly should be Montserrat light.
Nice to have
• Would be nice to see how this would look on mobile (as the application is responsive) but this is not mandatory.
Should not have
• Should not look too corporate or dry.

```html
<!DOCTYPE html>
<html lang="en">
<head>
<meta charset="utf-8">
<title>Bloom Path – Your Business</title>
<link href="https://fonts.googleapis.com/css2?family=Montserrat:wght@300;400;500;600&display=swap" rel="stylesheet">
<style>
  :root{
    --ink:#5c5c5c;
    --ink-dark:#2e2e30;
    --muted:#c2c4c6;
    --topbar:#3e3d40;
    --sky:#85cae6;
    --teal:#87cfc6;
    --orchid:#d2a4cc;
    --mist:#eef0f2;
    --line:#e3e5e7;
    --white:#ffffff;
  }
  *{box-sizing:border-box;margin:0;padding:0}
  html,body{width:1200px;height:2390px;overflow:hidden}
  body{font-family:"Montserrat",Arial,sans-serif;font-weight:300;color:var(--ink);background:var(--white);position:relative}

  /* top navigation */
  .topbar{position:absolute;left:0;top:0;width:1200px;height:51px;background:var(--topbar);color:var(--white);font-size:14px;font-weight:400}
  .brand{position:absolute;left:108px;top:14px;font-size:19px;font-weight:500;letter-spacing:0.5px}
  .topbar .tab{position:absolute;top:0;height:51px;line-height:51px}
  .tab-plan{left:308px;width:70px;text-align:center;background:var(--teal)}
  .tab-learn{left:400px}
  .tab-remember{left:478px}
  .tab-profile{left:943px}
  .tab-logout{left:1050px}

  .subnav{position:absolute;left:0;top:51px;width:1200px;height:51px;background:var(--sky);color:var(--white);font-size:13px;font-weight:400}
  .subnav .item{position:absolute;top:0;height:51px;line-height:51px}
  .subnav .active{left:99px;width:153px;text-align:center;background:var(--orchid)}

  /* intro */
  .client-mark{position:absolute;left:99px;top:164px;width:124px;height:124px;border-radius:50%;background:#111;color:var(--white);display:flex;align-items:center;justify-content:center;font-size:15px;font-weight:400;letter-spacing:1px}
  .intro-title{position:absolute;left:249px;top:162px;font-size:17px;font-weight:400;color:var(--ink-dark);letter-spacing:0.3px}
  .intro-copy{position:absolute;left:249px;top:197px;width:582px;font-size:11.6px;line-height:23px;color:var(--ink)}
  .intro-copy p+p{margin-top:0}
  .intro-photo{position:absolute;left:846px;top:164px;width:254px;height:260px;border:3px solid var(--white);box-shadow:0 0 0 1px var(--line);background:linear-gradient(135deg,#8a6a5a 0%,#d8a89a 40%,#e6c2b8 60%,#7c5f6a 100%)}

  /* who you are */
  .who{position:absolute;left:0;top:486px;width:1200px;height:888px;background:var(--mist)}
  .section-title{position:absolute;left:0;width:1200px;text-align:center;font-size:32px;font-weight:300;color:var(--ink-dark);letter-spacing:0.5px}
  .who .section-title{top:76px}
  .label{position:absolute;font-size:12.5px;font-weight:400;color:var(--ink-dark)}
  .field{position:absolute;height:40px;border-radius:20px;background:var(--white);font-size:11px;color:#a8aaac;line-height:40px;padding-left:28px;border:1px solid var(--line)}
  .upload{left:99px;top:191px;width:499px;overflow:hidden}
  .upload .browse{position:absolute;right:0;top:0;width:118px;height:40px;background:var(--sky);color:var(--white);text-align:center;font-size:11.5px;font-weight:500;letter-spacing:0.5px}
  .select::after{content:"";position:absolute;right:24px;top:18px;border:4px solid transparent;border-top-color:#555}
  .name-select{left:609px;top:191px;width:491px}
  .competitor-select{left:609px;top:461px;width:491px;height:38px;line-height:38px}
  .competitor-select::after{top:17px}

  .card{position:absolute;background:var(--white);border:1px solid var(--line)}
  .card-head{height:42px;line-height:42px;padding-left:15px;color:var(--white);font-size:13px;font-weight:400;position:relative}
  .card-body{padding:14px 15px;font-size:11px;line-height:23px;color:var(--muted)}
  .tip{position:absolute;right:12px;top:50%;width:21px;height:21px;margin-top:-10.5px;border-radius:50%;background:var(--white);text-align:center;line-height:21px;font-size:12px;font-weight:600}
  .card-orchid .card-head{background:var(--orchid)}
  .card-orchid .tip{color:var(--orchid)}
  .brand-card{top:263px;height:134px}

  .swatches{position:absolute;left:99px;top:461px;width:499px;height:38px;border-radius:19px;overflow:hidden;display:flex}
  .swatches span{flex:1}
  .marker{position:absolute;top:501px;width:0;height:0;border:8px solid transparent;border-bottom-color:#7a8a8a;border-top:0}

  .divider{position:absolute;left:99px;top:577px;width:1001px;height:1px;background:#dcdfe2}
  .swot-title{position:absolute;left:99px;top:627px;font-size:24px;font-weight:300;color:var(--ink-dark)}
  .swot{top:685px;height:118px;width:243px}
  .swot .card-head{height:35px;line-height:35px;background:var(--sky)}
  .swot .tip{color:var(--sky);width:20px;height:20px;line-height:20px;margin-top:-10px}
  .swot .card-body{line-height:22px}

  /* why you exist */
  .why .section-title{top:1428px}
  .q{width:492px;height:135px}
  .q .card-head{height:43px;line-height:43px;background:var(--teal);padding-left:21px;font-size:13px}
  .q .tip{color:var(--teal);right:20px}
  .q .card-body{padding:14px 21px}
  .col-l{left:99px}
  .col-r{left:609px}

  /* footer */
  .footer-rule{position:absolute;left:0;top:2301px;width:1200px;height:3px;background:var(--sky)}
  .footer-note{position:absolute;left:99px;top:2340px;font-size:12px;color:var(--ink)}
  .footer-note .sep{margin:0 8px;color:#aaa}
  .social{position:absolute;left:960px;top:2338px;display:flex;gap:20px}
  .social span{width:20px;height:20px;border-radius:50%}
</style>
</head>
<body>

<header class="topbar">
  <div class="brand">BLOOMPATH</div>
  <div class="tab tab-plan">Plan</div>
  <div class="tab tab-learn">Learn</div>
  <div class="tab tab-remember">Remember</div>
  <div class="tab tab-profile">My profile</div>
  <div class="tab tab-logout">Log out</div>
</header>

<nav class="subnav">
  <div class="item active">Your Business</div>
  <div class="item" style="left:288px">Your Products</div>
  <div class="item" style="left:449px">Your Customers</div>
  <div class="item" style="left:623px">Your Goals</div>
  <div class="item" style="left:762px">Your Plan</div>
</nav>

<section class="intro">
  <div class="client-mark">SOLENE</div>
  <h1 class="intro-title">SED UT PERSPICIATIS UNDE OMNIS</h1>
  <div class="intro-copy">
    <p>Nemo enim ipsam voluptatem quia voluptas sit aspernatur aut odit aut fugit, sed quia consequun-tur magni dolores eos qui ratione voluptatem sequi nesciunt. Neque porro quisquam est, qui dolorem ipsum quia dolor sit amet, consecte numquam eius modi tempora incidunt..</p>
    <p>Ut enim ad minima veniam, quis nostrum exercitationem ullam corporis suscipit laboriosam, nisi ut aliquid ex ea commodis autem vel eum iure repoluptate velit esse quam..</p>
    <p>Duis aute irure dolor in reprehenderit in voluptate velit esse cillum dolore eu fugiat nulla pariatur. Excepteur sint occaecat cupidatat non proidencia deserit anim id est laborum.Lorem ipsum dolor sit amet, con eiusmod tempor incididunt ut labore et dolore..</p>
  </div>
  <div class="intro-photo" role="img" aria-label="Photo of a makeup artist applying makeup to a smiling client"></div>
</section>

<section class="who">
  <h2 class="section-title">WHO YOU ARE</h2>

  <div class="label" style="left:99px;top:158px">Upload your Logo</div>
  <div class="field upload">Choose Logo<span class="browse">BROWSE</span></div>

  <div class="label" style="left:609px;top:158px">Business name</div>
  <div class="field select name-select">Sed ut perspiciatis unde omnis iste</div>

  <div class="card card-orchid brand-card" style="left:99px;width:328px">
    <div class="card-head">Business tag line<span class="tip">i</span></div>
    <div class="card-body">Quis nostrud exercitation ullamco laboris nisi ut aliqu unde omnis iste natust..</div>
  </div>
  <div class="card card-orchid brand-card" style="left:437px;width:326px">
    <div class="card-head">Business vision<span class="tip">i</span></div>
    <div class="card-body">Quis nostrud exercitation ullamco laboris nisi ut aliqu unde omnis iste natust..</div>
  </div>
  <div class="card card-orchid brand-card" style="left:773px;width:327px">
    <div class="card-head">Business bio<span class="tip">i</span></div>
    <div class="card-body">Quis nostrud exercitation ullamco laboris nisi ut aliqu unde omnis iste natust..</div>
  </div>

  <div class="label" style="left:99px;top:427px">Brand colours</div>
  <div class="swatches">
    <span style="background:#3d4a5f"></span><span style="background:#6a7a8d"></span><span style="background:#8fa3a3"></span>
    <span style="background:#0f5c5e"></span><span style="background:#1a7a6e"></span><span style="background:#7a9a6a"></span>
    <span style="background:#c9b05a"></span><span style="background:#d4a640"></span><span style="background:#c05a1c"></span>
    <span style="background:#e0662a"></span><span style="background:#f09a2a"></span><span style="background:#f3c21a"></span>
    <span style="background:#e86a10"></span><span style="background:#d01010"></span><span style="background:#c21818"></span>
    <span style="background:#a01820"></span><span style="background:#7a2828"></span><span style="background:#5a3a3a"></span>
    <span style="background:#6a8a70"></span><span style="background:#3e5a5a"></span><span style="background:#2a3a48"></span>
    <span style="background:#3a2a3a"></span>
  </div>
  <div class="marker" style="left:143px"></div>
  <div class="marker" style="left:511px;border-bottom-color:#5f7f68"></div>

  <div class="label" style="left:609px;top:427px">Key competitors</div>
  <div class="field select competitor-select">Sed ut perspiciatis unde omnis iste</div>

  <div class="divider"></div>
  <h3 class="swot-title">SWOT analysis</h3>

  <div class="card swot" style="left:99px">
    <div class="card-head">Strengths<span class="tip">i</span></div>
    <div class="card-body">Quis nostrud exercitation ullamco laboris nisomnis iste natust..</div>
  </div>
  <div class="card swot" style="left:352px">
    <div class="card-head">Weaknesses<span class="tip">i</span></div>
    <div class="card-body">Quis nostrud exercitation ulla..</div>
  </div>
  <div class="card swot" style="left:604px">
    <div class="card-head">Opportunities<span class="tip">i</span></div>
    <div class="card-body">Quis nostrun ullamco laboris nisomnis iste natust..</div>
  </div>
  <div class="card swot" style="left:857px">
    <div class="card-head">Threats<span class="tip">i</span></div>
    <div class="card-body">Exercitation ullamco laboris nisomnis iste natust..</div>
  </div>
</section>

<section class="why">
  <h2 class="section-title">WHY YOU EXIST</h2>

  <div class="card q col-l" style="top:1506px"><div class="card-head">Who are your ideal customers?<span class="tip">?</span></div><div class="card-body">Quis nostrud etation ullamco laboris xercitation ullamco laboris nisi ut aliqu unde omnis iste ncitation ullatust..</div></div>
  <div class="card q col-r" style="top:1506px"><div class="card-head">What problem are you trying to solve for them?<span class="tip">?</span></div><div class="card-body">Quis nostrud etation ullamco laboris xercitation ullamco laboris nisi ut aliqu unde omnis iste ncitation ullatust..</div></div>

  <div class="card q col-l" style="top:1656px"><div class="card-head">What pain points will this remove for them?<span class="tip">?</span></div><div class="card-body">Quis nostrud etation ullamco laboris xercitation ullamco laboris nisi ut aliqu unde omnis iste ncitation ullatust..</div></div>
  <div class="card q col-r" style="top:1656px"><div class="card-head">How do you solve it?<span class="tip">?</span></div><div class="card-body">Quis nostrud etation ullamco laboris xercitation ullamco laboris nisi ut aliqu unde omnis iste ncitation ullatust..</div></div>

  <div class="card q col-l" style="top:1806px"><div class="card-head">How else could this problem be solved?<span class="tip">?</span></div><div class="card-body">Quis nostrud etation ullamco laboris xercitation ullamco laboris nisi ut aliqu unde omnis iste ncitation ullatust..</div></div>
  <div class="card q col-r" style="top:1806px"><div class="card-head">Who offers these other solutions?<span class="tip">?</span></div><div class="card-body">Quis nostrud etation ullamco laboris xercitation ullamco laboris nisi ut aliqu unde omnis iste ncitation ullatust..</div></div>

  <div class="card q col-l" style="top:1954px"><div class="card-head">Why is your solution better?<span class="tip">?</span></div><div class="card-body">Quis nostrud etation ullamco laboris xercitation ullamco laboris nisi ut aliqu unde omnis iste ncitation ullatust..</div></div>
  <div class="card q col-r" style="top:1954px"><div class="card-head">How much does your solution cost?<span class="tip">?</span></div><div class="card-body">Quis nostrud etation ullamco laboris xercitation ullamco laboris nisi ut aliqu unde omnis iste ncitation ullatust..</div></div>

  <div class="card q col-l" style="top:2102px"><div class="card-head">What value are you providing to justify this cost?<span class="tip">?</span></div><div class="card-body">Quis nostrud etation ullamco laboris xercitation ullamco laboris nisi ut aliqu unde omnis iste ncitation ullatust..</div></div>
  <div class="card q col-r" style="top:2102px"><div class="card-head">How will this make their life/job easier/better?<span class="tip">?</span></div><div class="card-body">Quis nostrud etation ullamco laboris xercitation ullamco laboris nisi ut aliqu unde omnis iste ncitation ullatust..</div></div>
</section>

<footer>
  <div class="footer-rule"></div>
  <div class="footer-note">Copyright © Bloom Path 2017 All rights reserved<span class="sep">|</span>Privacy policy</div>
  <div class="social">
    <span style="background:#3b5998" role="img" aria-label="Social link 1"></span>
    <span style="background:#1da1f2" role="img" aria-label="Social link 2"></span>
    <span style="background:#dd4b39" role="img" aria-label="Social link 3"></span>
    <span style="background:#2a4a6a" role="img" aria-label="Social link 4"></span>
  </div>
</footer>

</body>
</html>
```